Fast quick flyer for Merchant Growth Fair

I am an information security consultant that needs to have a flyer and QUICK!!!
I need to get it to the printer today to have if done by monday. Quick turnaound.
I don't need the most amazing flyer but something that will capture their attention and offer them 40% off my base rate.
Updates

Here's some slight updates to the text, can you update and incorporate (PS: For some reason, when I initially put in Vantrel Systems, a " (quote) showed up, it's an apostrophe ( Vantrel Systems): Text: Vantrel Systems is the information security department for small and mid-sized businesses. Leveraging our 20+ years of information security experience, we will bring you the same level of service found at Pinnacle 300 companies. Small and mid-sized companies are often the target of malicious activity because they tend to lack the expertise to properly secure their environments. Now you can have your very own information security department at a fraction of the cost of a full time staff. Our typical rate for our premium offering: Guardline Plus is $5000/month based on a signed one year commitment. But for expo attendees, we are offering a special discount. As an expo attendee, you are eligible for a 40% discount. Guardline Plus for expo attendees will be $3000/month based on a signed one year commitment. Why put your company and your business at risk. Vantrel Systems is here to secure your company's future! Contact us now for more information: Leon Whitcombe Vantrel Systems "The information security department of small and mid-sized companies" 555-318-7292 info@vantrelsys.example http://www.vantrelsys.example

Also, this is going to be a 6x9 heavy stock postcard

Addition: Promo Code: GrowthFair 2014

Target Market(s)

Small businesses with a small IT department that can't afford to hire a full time IT Security Staff. We are the outsourced Information Security group

Industry/Entity Type

Small Business

Colors

Designer to choose colors to be used in the design.

Requirements
Must have
• Sell the idea that they need to take security serious and that we are the ones to do the job

Should stress that because they are attendees of the Merchant Growth Fair, they are eligible to get a 40% discount on our standard rate

```html
<!DOCTYPE html>
<html lang="en">
<head>
<meta charset="utf-8">
<title>Vantrel Systems – Expo Flyer</title>
<link href="https://fonts.googleapis.com/css2?family=Archivo+Black&family=Roboto+Condensed:wght@400;700&family=Arimo:wght@400;700&display=swap" rel="stylesheet">
<style>
  :root {
    --backdrop: #6b6b6b;
    --paper: #ffffff;
    --navy: #1f2a4a;
    --navy-deep: #172038;
    --sky: #1aa0e6;
    --sky-bright: #22aef0;
    --ink: #2b2b2b;
    --ink-soft: #444a55;
    --rule: #9aa0aa;
    --photo-dark: #0d1a3d;
    --photo-mid: #2a4aa0;
    --photo-light: #9fb8f0;
  }
  * { margin: 0; padding: 0; box-sizing: border-box; }
  html, body { width: 930px; height: 1200px; overflow: hidden; background: var(--backdrop); }
  .flyer {
    position: absolute; left: 50px; top: 52px; width: 830px; height: 1078px;
    background: var(--paper); overflow: hidden;
    font-family: "Arimo", Arial, sans-serif; color: var(--ink);
  }
  .brand { position: absolute; left: 58px; top: 50px; display: flex; align-items: center; gap: 12px; }
  .brand-mark { width: 52px; height: 52px; background: var(--navy); }
  .brand-name {
    font-family: "Roboto Condensed", sans-serif; font-weight: 700; font-size: 34px;
    line-height: 1; color: var(--navy); letter-spacing: 0.5px;
  }
  .hero {
    position: absolute; left: 0; top: 146px; width: 830px; height: 399px;
    background:
      radial-gradient(ellipse 180px 240px at 370px 170px, var(--photo-light), transparent 70%),
      linear-gradient(90deg, var(--photo-dark) 0%, var(--photo-mid) 35%, #4f6fd0 45%, var(--photo-mid) 58%, var(--photo-dark) 100%);
  }
  .hero-title { position: absolute; left: 70px; top: 272px; color: #fff; font-family: "Archivo Black", sans-serif; text-shadow: 0 2px 6px rgba(0,0,0,.45); }
  .hero-title .line-1 { display: block; font-size: 74px; line-height: 74px; letter-spacing: 1px; }
  .hero-title .line-2 { display: block; font-size: 35px; line-height: 40px; margin-top: 4px; }
  .hero-title .accent { color: var(--sky-bright); }
  .discount-badge {
    position: absolute; left: 626px; top: 70px; width: 154px; height: 156px;
    background: var(--sky); border: 4px solid #fff; border-radius: 14px;
    color: #fff; font-family: "Arimo", sans-serif; font-weight: 700; text-align: center;
    box-shadow: 0 2px 6px rgba(0,0,0,.3);
  }
  .discount-badge .figure { display: block; font-size: 60px; line-height: 60px; margin-top: 16px; }
  .discount-badge .caption { display: block; font-size: 19px; line-height: 20px; margin-top: 4px; text-align: left; padding-left: 14px; }
  .intro { position: absolute; left: 70px; top: 580px; width: 400px; font-size: 13.4px; line-height: 20px; color: var(--ink-soft); }
  .intro p + p { margin-top: 20px; }
  .intro strong { color: var(--ink); }
  .services { position: absolute; left: 68px; top: 738px; list-style: none; }
  .services li {
    display: flex; align-items: center; gap: 6px; height: 30px;
    font-family: "Roboto Condensed", sans-serif; font-weight: 700; font-size: 20px; color: var(--navy);
  }
  .offer { position: absolute; left: 70px; top: 836px; width: 420px; }
  .offer-head { font-size: 18.5px; line-height: 22px; color: var(--sky); }
  .offer-list { list-style: none; margin-top: 6px; font-size: 13px; line-height: 21px; color: var(--ink-soft); }
  .offer-list li { position: relative; padding-left: 18px; }
  .offer-list li::before { content: ""; position: absolute; left: 0; top: 6px; width: 9px; height: 9px; background: var(--navy); }
  .offer-list .hl { color: var(--sky); font-weight: 700; }
  .column-rule { position: absolute; left: 519px; top: 593px; width: 1px; height: 368px; background: var(--rule); }
  .side { position: absolute; left: 538px; font-family: "Roboto Condensed", sans-serif; }
  .side h2 { font-size: 17.5px; font-weight: 700; color: var(--sky); letter-spacing: .3px; }
  .side ul { list-style: none; margin-top: 6px; }
  .side li { position: relative; padding-left: 20px; font-size: 13px; color: var(--ink-soft); }
  .side li svg { position: absolute; left: 0; top: 2px; }
  .training { top: 593px; }
  .training li { line-height: 24px; }
  .consulting { top: 753px; }
  .consulting li { line-height: 15px; margin-bottom: 11px; }
  .courses-note {
    position: absolute; left: 693px; top: 630px; width: 104px; height: 104px; border-radius: 50%;
    background: var(--navy); color: var(--sky-bright); display: flex; align-items: center; justify-content: center;
    text-align: center; font-family: "Arimo", sans-serif; font-weight: 700; font-size: 14px; line-height: 17px;
  }
  .footer { position: absolute; left: 0; top: 950px; width: 830px; height: 128px; }
  .footer svg.band { position: absolute; left: 0; top: 0; }
  .contact-head { position: absolute; left: 30px; top: 28px; font-family: "Roboto Condensed", sans-serif; font-weight: 700; font-size: 19px; color: var(--sky-bright); }
  .contact-person { position: absolute; left: 31px; top: 66px; color: #fff; font-family: "Roboto Condensed", sans-serif; }
  .contact-person .name { display: block; font-weight: 700; font-size: 19px; letter-spacing: .3px; }
  .contact-person .role { display: block; font-size: 12px; font-weight: 700; margin-top: 3px; }
  .contact-rule { position: absolute; left: 240px; top: 66px; width: 1px; height: 42px; background: #fff; }
  .contact-lines { position: absolute; left: 260px; top: 64px; color: #fff; font-family: "Roboto Condensed", sans-serif; }
  .contact-lines .phone { display: flex; align-items: center; gap: 6px; font-weight: 700; font-size: 25px; line-height: 26px; }
  .contact-lines .email { display: flex; align-items: center; gap: 8px; font-weight: 700; font-size: 14px; margin-top: 4px; }
  .web { position: absolute; left: 590px; top: 90px; font-family: "Roboto Condensed", sans-serif; font-weight: 700; font-size: 19px; color: var(--sky-bright); }
</style>
</head>
<body>
<div class="flyer">
  <div class="brand">
    <span class="brand-mark"></span>
    <span class="brand-name">Vantrel Systems</span>
  </div>

  <div class="hero" role="img" aria-label="Photo of a server room corridor lit in blue, racks on both sides leading to a bright door"></div>
  <h1 class="hero-title">
    <span class="line-1">SECURING</span>
    <span class="line-2">THE <span class="accent">FUTURE</span> OF YOUR COMPANY</span>
  </h1>

  <div class="discount-badge">
    <span class="figure">40%</span>
    <span class="caption">DISCOUNT<br>FOR EXPO<br>ATTENDEES</span>
  </div>

  <div class="intro">
    <p><strong>Vantrel Systems</strong> as a information security department for small and mid-sized businesses.</p>
    <p>Small companies are targets because they lack the expertise at information security that large companies have.&nbsp; We have over 20 years of information security experience and we can leverage our expertise to give small companies the same level of security experience that Pinnacle 300 companies have.</p>
  </div>

  <ul class="services">
    <li><svg width="20" height="20" viewBox="0 0 20 20"><circle cx="10" cy="10" r="9.5" fill="#1aa0e6"/><path d="M5 10.5l3.3 3.2L15 7" stroke="#fff" stroke-width="2.6" fill="none"/></svg>Security Certification Courses</li>
    <li><svg width="20" height="20" viewBox="0 0 20 20"><circle cx="10" cy="10" r="9.5" fill="#1aa0e6"/><path d="M5 10.5l3.3 3.2L15 7" stroke="#fff" stroke-width="2.6" fill="none"/></svg>Information Security Consulting</li>
    <li><svg width="20" height="20" viewBox="0 0 20 20"><circle cx="10" cy="10" r="9.5" fill="#1aa0e6"/><path d="M5 10.5l3.3 3.2L15 7" stroke="#fff" stroke-width="2.6" fill="none"/></svg>Security Conferences</li>
  </ul>

  <div class="offer">
    <p class="offer-head">For expo attendees, we are offering<br>a special discount.</p>
    <ul class="offer-list">
      <li>Our monthly rate is $5000 (one year contract).</li>
      <li>For Expo attendees, we are offering a <span class="hl">40% discount.<br>Special Expo rate of $3000/month (one year contract).</span></li>
    </ul>
  </div>

  <div class="column-rule"></div>

  <section class="side training">
    <h2>TRAINING COURSES</h2>
    <ul>
      <li><svg width="12" height="12" viewBox="0 0 12 12"><circle cx="6" cy="6" r="5" fill="none" stroke="#1aa0e6" stroke-width="1.6"/><path d="M4 3.5L6.5 6 4 8.5M6.5 6H3" stroke="#1aa0e6" stroke-width="1.6" fill="none"/></svg>CISSP</li>
      <li><svg width="12" height="12" viewBox="0 0 12 12"><circle cx="6" cy="6" r="5" fill="none" stroke="#1aa0e6" stroke-width="1.6"/><path d="M4 3.5L6.5 6 4 8.5" stroke="#1aa0e6" stroke-width="1.6" fill="none"/></svg>CISM</li>
      <li><svg width="12" height="12" viewBox="0 0 12 12"><circle cx="6" cy="6" r="5" fill="none" stroke="#1aa0e6" stroke-width="1.6"/><path d="M4 3.5L6.5 6 4 8.5" stroke="#1aa0e6" stroke-width="1.6" fill="none"/></svg>Security+</li>
      <li><svg width="12" height="12" viewBox="0 0 12 12"><circle cx="6" cy="6" r="5" fill="none" stroke="#1aa0e6" stroke-width="1.6"/><path d="M4 3.5L6.5 6 4 8.5" stroke="#1aa0e6" stroke-width="1.6" fill="none"/></svg>ISO27k</li>
      <li><svg width="12" height="12" viewBox="0 0 12 12"><circle cx="6" cy="6" r="5" fill="none" stroke="#1aa0e6" stroke-width="1.6"/><path d="M4 3.5L6.5 6 4 8.5" stroke="#1aa0e6" stroke-width="1.6" fill="none"/></svg>Dedicated Classes</li>
    </ul>
  </section>

  <div class="courses-note">A variety<br>of courses for<br>the security<br>practitioner</div>

  <section class="side consulting">
    <h2>CONSULTING</h2>
    <ul>
      <li><svg width="12" height="12" viewBox="0 0 12 12"><circle cx="6" cy="6" r="5" fill="none" stroke="#1aa0e6" stroke-width="1.6"/><path d="M4 3.5L6.5 6 4 8.5" stroke="#1aa0e6" stroke-width="1.6" fill="none"/></svg>Guardline Plus (a top tier service)</li>
      <li><svg width="12" height="12" viewBox="0 0 12 12"><circle cx="6" cy="6" r="5" fill="none" stroke="#1aa0e6" stroke-width="1.6"/><path d="M4 3.5L6.5 6 4 8.5" stroke="#1aa0e6" stroke-width="1.6" fill="none"/></svg>Legal Information Security and Protection<br>&nbsp;(our new offering)</li>
      <li><svg width="12" height="12" viewBox="0 0 12 12"><circle cx="6" cy="6" r="5" fill="none" stroke="#1aa0e6" stroke-width="1.6"/><path d="M4 3.5L6.5 6 4 8.5" stroke="#1aa0e6" stroke-width="1.6" fill="none"/></svg>Health Information Security and Protection</li>
      <li><svg width="12" height="12" viewBox="0 0 12 12"><circle cx="6" cy="6" r="5" fill="none" stroke="#1aa0e6" stroke-width="1.6"/><path d="M4 3.5L6.5 6 4 8.5" stroke="#1aa0e6" stroke-width="1.6" fill="none"/></svg>Company Wide Policies and Procedures</li>
      <li><svg width="12" height="12" viewBox="0 0 12 12"><circle cx="6" cy="6" r="5" fill="none" stroke="#1aa0e6" stroke-width="1.6"/><path d="M4 3.5L6.5 6 4 8.5" stroke="#1aa0e6" stroke-width="1.6" fill="none"/></svg>Security Reviews and Risk Assessments</li>
      <li><svg width="12" height="12" viewBox="0 0 12 12"><circle cx="6" cy="6" r="5" fill="none" stroke="#1aa0e6" stroke-width="1.6"/><path d="M4 3.5L6.5 6 4 8.5" stroke="#1aa0e6" stroke-width="1.6" fill="none"/></svg>General IT Consulting, Management<br>&nbsp;and Outsourcing</li>
    </ul>
  </section>

  <footer class="footer">
    <svg class="band" width="830" height="128" viewBox="0 0 830 128">
      <path d="M0 8 Q0 8 8 8 H465 C505 8 500 72 560 72 H830 V128 H0 Z" fill="#1f2a4a"/>
    </svg>
    <p class="contact-head">For More Information Contact:</p>
    <p class="contact-person"><span class="name">LEON WHITCOMBE</span><span class="role">Chief Security Consultant</span></p>
    <div class="contact-rule"></div>
    <div class="contact-lines">
      <p class="phone"><svg width="18" height="18" viewBox="0 0 18 18"><circle cx="9" cy="9" r="8" fill="none" stroke="#fff" stroke-width="1.5"/><path d="M6.3 4.8c-.9.6-1 2.2.2 4.3s2.8 3.5 3.9 3.3l.9-1.4-1.6-1.1-.7.6c-.5-.2-1.3-1.1-1.6-1.8l.6-.7-1-1.7z" fill="#fff"/></svg>555-318-7292</p>
      <p class="email"><svg width="14" height="10" viewBox="0 0 14 10"><rect width="14" height="10" fill="#fff"/><path d="M0 0l7 5.5L14 0" stroke="#1f2a4a" stroke-width="1.3" fill="none"/></svg>leon.whitcombe@vantrelsys.example</p>
    </div>
    <p class="web">www.vantrelsys.example</p>
  </footer>
</div>
</body>
</html>
```